BRISKEL Need a luxury modern business card designed.

Need a luxury modern business card designed. refer to the uploaded files for the company name and logo in the zip file under source files. i will making my descion on monday. so please send in before then so if we need to edit we will have the time. we have a trade show coming up and im on a deadline for printer.

Target Market(s)

high end clients

Contact Information for Business Card

Company nAme and logo. Tobias Fennick Co-Founder / Project Manager Office # 555-318-7094 Cell # 555-642-1586 BRISKEL.CA Tobias@briskel-example.ca

Font styles to use
Other font styles liked:
• Modern

Requirements
Must have
• Company name and logo, contact info, using the black, gold and white color scheme.

```html
<!DOCTYPE html>
<html lang="en">
<head>
<meta charset="utf-8">
<title>BRISKEL Business Card</title>
<link rel="stylesheet" href="https://fonts.googleapis.com/css2?family=Poppins:wght@300;400;500&display=swap">
<style>
  :root {
    --backdrop: #2a2a2d;
    --card: #1f2123;
    --white: #f4f4f2;
    --gold: #b59a5f;
    --grey: #9a9a98;
  }
  * { margin: 0; padding: 0; box-sizing: border-box; }
  html, body { width: 1200px; height: 800px; overflow: hidden; }
  body {
    background: var(--backdrop);
    font-family: "Poppins", sans-serif;
    display: flex;
    flex-direction: column;
    align-items: center;
    justify-content: center;
    gap: 48px;
  }
  .card {
    width: 595px;
    height: 340px;
    background: var(--card);
    border-radius: 18px;
    box-shadow: 0 14px 34px rgba(0,0,0,0.45);
    position: relative;
    overflow: hidden;
  }
  .card-front {
    display: flex;
    align-items: center;
    justify-content: center;
  }
  .brand {
    display: flex;
    align-items: center;
    gap: 18px;
  }
  .brand-square {
    width: 22px;
    height: 22px;
    background: var(--gold);
  }
  .brand-name {
    font-weight: 300;
    color: var(--white);
    letter-spacing: 0.14em;
  }
  .card-front .brand-name { font-size: 52px; }
  .card-back { display: flex; }
  .back-brand {
    flex: 0 0 56%;
    display: flex;
    align-items: center;
    justify-content: center;
  }
  .back-brand .brand-name { font-size: 38px; }
  .back-brand .brand-square { width: 16px; height: 16px; }
  .divider {
    width: 1px;
    margin: 58px 0;
    background: linear-gradient(to bottom, transparent, var(--gold) 20%, var(--gold) 80%, transparent);
  }
  .contact {
    flex: 1;
    padding: 0 0 0 30px;
    display: flex;
    flex-direction: column;
    justify-content: center;
  }
  .person-name {
    font-size: 21px;
    font-weight: 400;
    color: var(--white);
    letter-spacing: 0.01em;
  }
  .person-name .surname { color: var(--gold); }
  .person-title {
    font-size: 12px;
    font-weight: 300;
    color: var(--grey);
    margin: 2px 0 22px;
  }
  .contact-list { list-style: none; }
  .contact-item {
    display: flex;
    align-items: center;
    gap: 12px;
    font-size: 13px;
    color: var(--white);
    line-height: 1.85;
  }
  .contact-item svg { width: 13px; height: 13px; flex: none; }
</style>
</head>
<body>
  <section class="card card-front">
    <div class="brand">
      <span class="brand-square"></span>
      <span class="brand-name">BRISKEL</span>
    </div>
  </section>

  <section class="card card-back">
    <div class="back-brand">
      <div class="brand">
        <span class="brand-square"></span>
        <span class="brand-name">BRISKEL</span>
      </div>
    </div>
    <div class="divider"></div>
    <div class="contact">
      <h1 class="person-name">TOBIAS <span class="surname">FENNICK</span></h1>
      <p class="person-title">Co-Founder / Project Manager</p>
      <ul class="contact-list">
        <li class="contact-item">
          <svg viewBox="0 0 16 16" fill="#f4f4f2"><path d="M3 6c0-2 2-3 5-3s5 1 5 3l-2 1-1-2H6L5 7zM4 8h8l1 5H3z"/></svg>
          555-318-7094
        </li>
        <li class="contact-item">
          <svg viewBox="0 0 16 16" fill="none" stroke="#f4f4f2" stroke-width="1.6"><rect x="4" y="1.5" width="8" height="13" rx="1.5"/></svg>
          555-642-1586
        </li>
        <li class="contact-item">
          <svg viewBox="0 0 16 16" fill="none" stroke="#f4f4f2" stroke-width="1.3"><circle cx="8" cy="8" r="6.5"/><ellipse cx="8" cy="8" rx="3" ry="6.5"/><path d="M1.5 8h13"/></svg>
          BRISKEL.CA
        </li>
        <li class="contact-item">
          <svg viewBox="0 0 16 16" fill="#f4f4f2"><path d="M1 3h14v10H1z"/><path d="M1 3l7 6 7-6" fill="none" stroke="#1f2123" stroke-width="1.3"/></svg>
          Tobias@briskel-example.ca
        </li>
      </ul>
    </div>
  </section>
</body>
</html>
```